Realtor branding business card

modern, simple and self branding. Broker office logo needs to be used but not emphasized. Looking to brand myself

Target Market(s)

buyers, sellers and investors

Industry/Entity Type

Realtor

Contact Information for Business Card

Sample of my current business card on file

Requirements
Must have
• my website - tobiasmerrowkl.com
• Realtor logo
• Fair housing logo
Nice to have
• Colors from office logo but not a must
Should not have
• Do not want headshot

```html
<!DOCTYPE html>
<html lang="en">
<head>
<meta charset="utf-8">
<title>Tobias Merrow – Realtor Business Card</title>
<link href="https://fonts.googleapis.com/css2?family=Lato:wght@400;700;900&family=Libre+Baskerville:wght@700&display=swap" rel="stylesheet">
<style>
  :root {
    --navy: #1b3a5c;
    --navy-deep: #142b44;
    --navy-bright: #22649a;
    --royal: #1f4ea3;
    --paper: #ffffff;
    --ink: #3b3b3b;
    --ground: #e6e9ee;
    --ground-edge: #b9c3cf;
  }
  * { margin: 0; padding: 0; box-sizing: border-box; }
  html, body { width: 1200px; height: 675px; overflow: hidden; }
  body {
    background: radial-gradient(ellipse at 40% 60%, var(--ground) 0%, var(--ground-edge) 100%);
    font-family: 'Lato', sans-serif;
    position: relative;
  }
  .card {
    position: absolute;
    top: 187px;
    width: 525px;
    height: 300px;
    box-shadow: 0 10px 30px rgba(30, 45, 65, 0.25);
    overflow: hidden;
  }
  /* Front */
  .card-front { left: 45px; background: var(--paper); }
  .identity {
    position: absolute; top: 30px; right: 34px; text-align: right;
  }
  .agent-name {
    font-family: 'Libre Baskerville', serif;
    font-weight: 700; font-size: 21px; color: var(--ink);
  }
  .agent-title {
    font-size: 15px; color: var(--royal); letter-spacing: 0.5px; margin-top: 4px;
  }
  .brokerage {
    position: absolute; top: 72px; left: 30px;
    display: flex; align-items: center; gap: 8px;
  }
  .brokerage-dot { width: 12px; height: 12px; background: var(--royal); }
  .brokerage-name {
    font-weight: 900; font-size: 17px; color: var(--royal); line-height: 1.05;
  }
  .contact-band {
    position: absolute; top: 118px; left: 0; right: 0; height: 78px;
    background: linear-gradient(90deg, var(--navy-deep) 0%, var(--navy) 55%, var(--navy-bright) 100%);
    color: var(--paper);
    display: flex; align-items: center; justify-content: space-between;
    padding: 0 30px; font-size: 13px;
  }
  .contact-item { display: flex; flex-direction: column; align-items: center; gap: 6px; text-align: center; }
  .contact-item svg { width: 16px; height: 16px; }
  .social-dot { width: 14px; height: 14px; border-radius: 50%; background: var(--paper); }
  .address {
    position: absolute; top: 214px; right: 34px;
    display: flex; gap: 8px; font-size: 13px; color: var(--ink); line-height: 1.4;
  }
  .address svg { width: 12px; height: 16px; margin-top: 2px; }
  .badges { position: absolute; bottom: 26px; left: 30px; display: flex; gap: 10px; }
  .badge { width: 24px; height: 22px; background: #6b6b6b; }
  .badge-round { border-radius: 50%; width: 22px; }
  /* Back */
  .card-back {
    left: 630px;
    background: radial-gradient(ellipse at 65% 35%, var(--navy-bright) 0%, var(--navy) 45%, var(--navy-deep) 100%);
    color: var(--paper);
    display: flex; flex-direction: column; align-items: center; justify-content: center;
  }
  .back-brand { display: flex; align-items: center; gap: 14px; }
  .back-brand-mark { width: 22px; height: 22px; background: var(--paper); }
  .back-brand-name { font-weight: 900; font-size: 38px; line-height: 1.05; }
  .website { margin-top: 40px; font-size: 15px; letter-spacing: 0.5px; }
</style>
</head>
<body>
  <section class="card card-front">
    <div class="identity">
      <p class="agent-name">Tobias Merrow, PA</p>
      <p class="agent-title">REALTOR</p>
    </div>
    <div class="brokerage">
      <span class="brokerage-dot"></span>
      <span class="brokerage-name">Northgate<br>Realty Group</span>
    </div>
    <div class="contact-band">
      <div class="contact-item">
        <span class="social-dot"></span>
        <span>@tobiasmerrowkl</span>
      </div>
      <div class="contact-item">
        <svg viewBox="0 0 16 16"><circle cx="8" cy="8" r="8" fill="#fff"/><path d="M5.2 4.2l1.5-.3.8 1.9-1 .8a5.5 5.5 0 0 0 2.9 2.9l.8-1 1.9.8-.3 1.5c-3.6.3-6.9-3-6.6-6.6z" fill="#1b3a5c"/></svg>
        <span>Cell : 555 218 4093<br>Office : 555 640 1750</span>
      </div>
      <div class="contact-item">
        <svg viewBox="0 0 16 16"><circle cx="8" cy="8" r="8" fill="#fff"/><rect x="4" y="5.2" width="8" height="5.6" fill="#1b3a5c"/><path d="M4 5.4l4 3 4-3" stroke="#fff" stroke-width="0.8" fill="none"/></svg>
        <span>merrowrealty@mailbox.com</span>
      </div>
    </div>
    <div class="address">
      <svg viewBox="0 0 12 16"><path d="M6 0a6 6 0 0 0-6 6c0 4.5 6 10 6 10s6-5.5 6-10a6 6 0 0 0-6-6z" fill="#1f4ea3"/><circle cx="6" cy="6" r="2.2" fill="#fff"/></svg>
      <span>48 Linden Crest Avenue.<br>Cedar Hollow. FL 30000</span>
    </div>
    <div class="badges">
      <span class="badge" role="img" aria-label="Fair housing badge"></span>
      <span class="badge badge-round" role="img" aria-label="Realtor membership badge"></span>
    </div>
  </section>

  <section class="card card-back">
    <div class="back-brand">
      <span class="back-brand-mark"></span>
      <span class="back-brand-name">Northgate<br>Realty Group</span>
    </div>
    <p class="website">www.tobiasmerrowkl.com</p>
  </section>
</body>
</html>
```